Corvena Hotel, city center modern minimal hotel operating all year round, on Rhodes island Greece

city, modern ,all year operating hotel

Target Market(s)

tourists, business agents

Industry/Entity Type

tourism

Number of Pages Required

2 page

Requirements
Must have
• room type photos and descriptions, amenities individual listing (graphic), comments sections, map driving location details
Nice to have
• gallery section, modern and minimal design, amenities section, individual room type descriptions, photos and facilities

```html
<!DOCTYPE html>
<html lang="en">
<head>
<meta charset="utf-8">
<title>Corvena Hotel</title>
<link href="https://fonts.googleapis.com/css2?family=Playfair+Display:wght@600;700&family=Hind:wght@300;400;500;600&display=swap" rel="stylesheet">
<style>
:root{
  --green:#1d4a2b;
  --green-dark:#153a21;
  --gold:#c39a3a;
  --gold-dark:#7a5a1c;
  --ink:#2b2b2b;
  --muted:#555;
  --line:#e6e6e6;
  --panel:#151515;
  --white:#fff;
}
*{box-sizing:border-box;margin:0;padding:0}
html,body{width:1200px;height:4237px;overflow:hidden}
body{position:relative;background:var(--white);font-family:"Hind",sans-serif;color:var(--ink)}
.abs{position:absolute}
.serif{font-family:"Playfair Display",serif}

/* header */
.brand{display:flex;align-items:center;gap:12px;font-family:"Hind",sans-serif;font-weight:500;color:var(--green);font-size:30px;letter-spacing:1px}
.brand-dot{width:30px;height:30px;border-radius:50%;background:var(--green)}
.nav a{position:absolute;top:38px;font-size:15px;color:var(--ink);text-decoration:none}
.btn-book{left:948px;top:30px;width:106px;height:39px;border:2px solid var(--green);border-radius:20px;font-size:15px;display:flex;align-items:center;justify-content:center;color:var(--green-dark)}

/* hero */
.hero{left:0;top:98px;width:1200px;height:543px;background:linear-gradient(180deg,#b8892f 0%,#8d6a2c 35%,#4a3b25 75%,#2c2519 100%)}
.hero-mark{left:214px;top:140px;width:150px;height:107px;display:flex;align-items:center;justify-content:center}
.hero-mark span{width:96px;height:96px;border-radius:50%;background:var(--green);border:4px solid var(--white)}
.hero-title{left:383px;top:128px;font-size:22px;color:#111}
.hero-title b{font-family:"Playfair Display",serif;font-size:38px;color:var(--green);font-weight:700}
.hero-text{left:383px;top:186px;width:430px;font-size:16px;line-height:26px;color:#1c1c1c}
.btn-start{left:383px;top:255px;width:107px;height:38px;border-radius:19px;background:#111;color:var(--white);font-size:15px;display:flex;align-items:center;justify-content:center}
.map{left:842px;top:127px;width:200px;height:152px;background:linear-gradient(135deg,#f1f1ef,#dcdcd8);border:1px solid #ccc}

/* booking */
.booking{left:168px;top:520px;width:863px;height:516px;background:var(--white);box-shadow:0 2px 14px rgba(0,0,0,.12);border-radius:4px}
.booking h1{position:absolute;left:0;top:30px;width:100%;text-align:center;font-family:"Playfair Display",serif;font-size:46px;color:var(--green);font-weight:700}
.booking .sub{position:absolute;left:0;top:96px;width:100%;text-align:center;font-size:16px}
.field{position:absolute;height:65px;border-radius:6px;box-shadow:0 1px 8px rgba(0,0,0,.12);font-size:16px;display:flex;align-items:center;padding:0 20px;justify-content:space-between}
.field.sel{justify-content:space-around;font-size:13px;height:69px}
.chk{position:absolute;left:442px;top:345px;display:flex;align-items:center;gap:14px;font-size:16px}
.chk i{width:20px;height:20px;border:2px solid #777;border-radius:3px;display:block}
.btn-submit{left:67px;top:415px;width:722px;height:58px;border-radius:29px;background:var(--green);color:var(--white);font-size:17px;display:flex;align-items:center;justify-content:center}

/* services */
.h2{width:1200px;left:0;text-align:center;font-family:"Playfair Display",serif;font-weight:700;color:var(--green);font-size:38px}
.svc{top:1167px;width:226px;height:489px;background:var(--white);box-shadow:0 1px 10px rgba(0,0,0,.14);padding:20px 18px}
.svc svg{display:block;margin:0 auto}
.svc h3{text-align:center;font-family:"Playfair Display",serif;color:var(--green);font-size:19px;margin:28px 0 26px}
.svc p{font-size:14px;line-height:24px;text-align:justify;color:#333;margin-bottom:24px}

/* about */
.about-mark{left:145px;top:1746px;width:172px;height:128px;display:flex;align-items:center;justify-content:center}
.about-mark span{width:96px;height:96px;border-radius:50%;background:var(--green)}
.score{left:159px;top:1932px;width:147px;height:144px;background:#1c3a78}
.about{left:339px;top:1746px;width:861px;height:434px;background:var(--panel);border-radius:18px 0 0 0;color:#eee;padding:26px 80px 0 26px;font-size:14.5px;line-height:25.5px}
.about p{margin-bottom:25px}
.award{top:2211px;height:112px;border:2px solid #777}

/* rooms */
.tab{top:2471px;height:43px;border:1px solid var(--line);box-shadow:0 1px 6px rgba(0,0,0,.1);font-size:18px;display:flex;align-items:center;justify-content:center}
.tab.on{background:var(--green);color:var(--white)}
.room-desc{left:170px;top:2562px;width:860px;text-align:center;font-size:16.5px;line-height:28px}
.photo{width:268px;height:251px}
.btn-more{left:526px;top:3234px;width:148px;height:39px;border-radius:20px;background:var(--green);color:var(--white);font-size:16px;display:flex;align-items:center;justify-content:center}

/* testimonials */
.tsub{left:0;width:1200px;text-align:center;top:3382px;font-size:16px}
.tcard{top:3433px;width:284px;height:416px;background:var(--white);box-shadow:0 1px 10px rgba(0,0,0,.14);overflow:hidden}
.tcard .quote{position:absolute;left:20px;top:18px;font-family:"Playfair Display",serif;font-size:60px;color:#ddd;line-height:1}
.tcard p{position:absolute;left:22px;top:44px;width:240px;text-align:center;font-size:12.5px;line-height:27px;color:#333}
.tcard svg{position:absolute;left:0;top:250px}
.avatar{position:absolute;left:97px;top:252px;width:92px;height:92px;border-radius:50%;background:radial-gradient(circle at 50% 40%,#d8b79a,#8a6b55);border:3px solid var(--white)}
.tcard h4{position:absolute;left:0;width:100%;bottom:22px;text-align:center;color:var(--white);font-family:"Playfair Display",serif;font-size:18px}

/* footer */
.rule{left:0;width:1200px;height:1px;background:#ccc}
.foot-brand{left:145px;top:3990px;font-size:44px;flex-direction:column;gap:10px;align-items:flex-start}
.contact{left:419px;font-size:13.5px;display:flex;align-items:center;gap:10px}
.fcol h5{font-size:15px;font-weight:600;letter-spacing:.5px;margin-bottom:14px}
.fcol a{display:block;font-size:14px;color:var(--ink);text-decoration:none;margin-bottom:13px}
.copy{left:145px;top:4180px;font-size:12.5px}
</style>
</head>
<body>

<header>
  <div class="abs brand" style="left:145px;top:30px"><span class="brand-dot"></span>Corvena Hotel</div>
  <nav class="nav">
    <a style="left:618px">Home</a>
    <a style="left:699px">Rooms</a>
    <a style="left:781px">Gallery</a>
    <a style="left:863px">Contact</a>
  </nav>
  <div class="abs btn-book">Book Now</div>
</header>

<section class="abs hero" role="img" aria-label="Hotel lobby interior with warm golden lighting"></section>
<div class="abs hero-mark"><span></span></div>
<div class="abs hero-title">Welcome to <b>Corvena Hotel</b></div>
<p class="abs hero-text">Lorem ipsum dolor sit amet, consectetur adipiscing elit, sed do eiusmod tempor incididunt ut labore et dolore magna aliqua.</p>
<div class="abs btn-start">Get Started</div>
<div class="abs map" role="img" aria-label="Street map showing the hotel location in Rhodes town"></div>

<section class="abs booking">
  <h1>CORVENA CITY HOTEL RHODES</h1>
  <div class="sub">ONE OF THE BEST PLACES TO RELAX &amp; ENJOY</div>
  <div class="field" style="left:72px;top:152px;width:349px">Full Name*</div>
  <div class="field" style="left:442px;top:152px;width:347px">Email*</div>
  <div class="field" style="left:72px;top:238px;width:349px">Arrival Date
    <svg width="20" height="20" viewBox="0 0 20 20" fill="none" stroke="#555" stroke-width="1.5"><rect x="2" y="4" width="16" height="14" rx="2"/><path d="M2 8h16M6 2v4M14 2v4M6 11h2M10 11h2M14 11h1M6 14h2M10 14h2"/></svg></div>
  <div class="field" style="left:442px;top:238px;width:347px">Depature Date
    <svg width="20" height="20" viewBox="0 0 20 20" fill="none" stroke="#555" stroke-width="1.5"><rect x="2" y="4" width="16" height="14" rx="2"/><path d="M2 8h16M6 2v4M14 2v4M6 11h2M10 11h2M14 11h1M6 14h2M10 14h2"/></svg></div>
  <div class="field sel" style="left:72px;top:323px;width:349px">
    <span>Rooms &#8964;</span><span>Adults &#8964;</span><span>Children &#8964;</span></div>
  <div class="chk"><i></i>I Have Read And Agree With The Terms</div>
  <div class="abs btn-submit">Submit</div>
</section>

<h2 class="abs h2" style="top:1078px">Services</h2>

<article class="abs svc" style="left:123px">
  <svg width="40" height="44" viewBox="0 0 40 44" fill="none" stroke="#444" stroke-width="1.5"><rect x="4" y="12" width="30" height="28"/><circle cx="28" cy="10" r="7"/><path d="M28 17l-4-5M4 32l10-10 10 10M20 28l6-6 8 8"/></svg>
  <h3>Location</h3>
  <p>Medieval city is just a few steps away, so are the beautiful beaches of Elli and Psaropoula.</p>
  <p>New market is available all around the hotel, with lots of commercial shops like Stylo, Marcell, etc.. just to name a few.</p>
  <p>Food strict is also right around the corner with Burger Point, local street food and Pizza places.</p>
</article>
<article class="abs svc" style="left:365px">
  <svg width="40" height="50" viewBox="0 0 40 50" fill="none" stroke="#444" stroke-width="1.5"><rect x="3" y="4" width="34" height="44"/><path d="M3 12h34M8 18h6v6H8zM17 18h6v6h-6zM26 18h6v6h-6zM8 28h6v6H8zM17 28h6v6h-6zM26 28h6v6h-6zM8 38h6v6H8zM26 38h6v6h-6z"/></svg>
  <h3>Operation</h3>
  <p>Famous for its friendliness, cleanliness and various amenities found only in higher category establishments.</p>
  <p>Offering American enhanced breakfast from 07:30 until 11:00 daily, and a lounge cafe with lunch and dinner at your leisure</p>
</article>
<article class="abs svc" style="left:608px">
  <svg width="44" height="44" viewBox="0 0 44 44" fill="none" stroke="#444" stroke-width="1.5"><path d="M22 14c-4-8-18-6-16 4 2 8 16 18 16 18s14-10 16-18c2-10-12-12-16-4z"/><path d="M8 30l8 8h12l8-8"/></svg>
  <h3>Friendliness</h3>
  <p>The hotel offers its services to both local and international guests either family or business type.</p>
  <p>Corvena staff acts more like family than employees as most of them have been around for so many years, that are technically a family by now, and this attitude is evident throughout all the sections of the hotel by everyone.</p>
</article>
<article class="abs svc" style="left:850px">
  <svg width="44" height="48" viewBox="0 0 44 48" fill="none" stroke="#444" stroke-width="1.5"><path d="M6 20h32v16H6zM10 36v6M34 36v6M6 26h32M18 8h10v12M28 4l6 4"/><circle cx="12" cy="44" r="2"/><circle cx="32" cy="44" r="2"/></svg>
  <h3>Amenities</h3>
  <p>The hotel offers most modern amenities, like satellite television set, mini bar, en sure bathroom with amenities, hairdryer, safe storage area for valuables, laminated flooring, double glazed windows and balcony.</p>
  <p>A lounge sun deck area is also provided on the roof of the hotel, ideal for sunbathing and relaxing under the sun.</p>
</article>

<div class="abs about-mark"><span></span></div>
<div class="abs score" aria-label="Guest review award badge"></div>
<section class="abs about">
  <p>Situated at the very heart of Rhodes town, the hotel provides easy access to all major points of interest all within walking distance.</p>
  <p>The hotel is renowned in the local market due to its operation which “runs” 365 days a year. All rooms have been renovated recently and offer a unique design with modern furnishes. Being in constant operation for the last 47 years, and gone through numerous renovations the hotel operates mainly with repeaters who value and appreciate its comfort, cleanliness, family attitude, amenities and personality just to name a few.</p>
  <p>On line booking is available through mainstream agencies or directly with the hotel, with its own platform at www.corvenahotel.com were various offers are available all through the year.</p>
  <p>Our reception operates 24 hours and 7 days a week, making check in or providing information a breeze. All the information one might need for sightseeing the island either by boat, bike, car or motorbike is available here. Tickets for shows, boat trips or museums are also available, as well as car hire from the hotels own rental company, offering lower rates than any competitor local or otherwise.</p>
</section>

<div class="abs award" style="left:168px;width:119px"></div>
<div class="abs award" style="left:353px;width:119px"></div>
<div class="abs award" style="left:537px;width:122px"></div>
<div class="abs" style="left:730px;top:2215px;width:86px;height:104px;border-radius:50%;border:3px solid #111"></div>
<div class="abs" style="left:873px;top:2244px;width:164px;height:46px;border-radius:23px;background:#d32f2f;opacity:.85"></div>

<h2 class="abs h2" style="top:2390px">Rooms Gallery</h2>
<div class="abs tab on" style="left:215px;width:107px">Single</div>
<div class="abs tab" style="left:342px;width:110px">Double</div>
<div class="abs tab" style="left:470px;width:102px">Triple</div>
<div class="abs tab" style="left:595px;width:109px">Quadruple</div>
<div class="abs tab" style="left:718px;width:147px">Superior Double</div>
<div class="abs tab" style="left:881px;width:107px">Apartment</div>
<p class="abs room-desc">This comfortable room features a balcony, laminated floors, private bathroom with shower, office desk, satellite TV and other Amenities.</p>

<div class="abs photo" style="left:145px;top:2632px;background:linear-gradient(160deg,#a8a27f,#4d4535 70%,#1e1a14)" role="img" aria-label="Single room with bed and patterned wall"></div>
<div class="abs photo" style="left:465px;top:2632px;background:linear-gradient(160deg,#6a4a36,#8a5b3f 50%,#3a2a20)" role="img" aria-label="Single room with wood panelling and bed"></div>
<div class="abs photo" style="left:784px;top:2632px;background:linear-gradient(160deg,#c7b392,#6b5234 60%,#2d241a)" role="img" aria-label="Single room with decorative headboard wall"></div>
<div class="abs photo" style="left:145px;top:2933px;background:linear-gradient(160deg,#b08e3f,#5e4a22 60%,#2a2112)" role="img" aria-label="Single room with desk and television"></div>
<div class="abs photo" style="left:465px;top:2933px;background:linear-gradient(160deg,#e4d6c2,#8a6a52 60%,#3a2c22)" role="img" aria-label="Single room with bed and bright wall art"></div>
<div class="abs photo" style="left:784px;top:2933px;background:linear-gradient(160deg,#8a5f3e,#d9cbb6 45%,#4a3224)" role="img" aria-label="Single room with striped bedspread"></div>
<div class="abs btn-more">View More</div>

<h2 class="abs h2" style="top:3322px">Testimonials</h2>
<p class="abs tsub">Lovely people - Amazing experiences</p>

<article class="abs tcard" style="left:143px">
  <span class="quote">“</span>
  <p>Stavros welcomed us with a very generous touch, Authentic Greek Hospitality, If you wan to experience a genuine village experience with the communtiy, and savor the magnificent viewing in the streets, like postal cards, well this is the right place away from the touristic crowd, I loved it!!</p>
  <svg width="284" height="166" viewBox="0 0 284 166"><path d="M0 40 C60 20 110 110 180 70 C230 40 260 10 284 20 V166 H0z" fill="var(--green)"/></svg>
  <div class="avatar" role="img" aria-label="Guest portrait"></div>
  <h4>Marc Delaunay</h4>
</article>
<article class="abs tcard" style="left:457px">
  <span class="quote">“</span>
  <p>Stavros welcomed us with a very generous touch, Authentic Greek Hospitality, If you wan to experience a genuine village experience with the communtiy, and savor the magnificent viewing in the streets, like postal cards, well this is the right place away from the touristic crowd, I loved it!!</p>
  <svg width="284" height="166" viewBox="0 0 284 166"><path d="M0 40 C60 20 110 110 180 70 C230 40 260 10 284 20 V166 H0z" fill="var(--green)"/></svg>
  <div class="avatar" role="img" aria-label="Guest portrait"></div>
  <h4>Tomas Rein</h4>
</article>
<article class="abs tcard" style="left:769px">
  <span class="quote">“</span>
  <p>Stavros welcomed us with a very generous touch, Authentic Greek Hospitality, If you wan to experience a genuine village experience with the communtiy, and savor the magnificent viewing in the streets, like postal cards, well this is the right place away from the touristic crowd, I loved it!!</p>
  <svg width="284" height="166" viewBox="0 0 284 166"><path d="M0 40 C60 20 110 110 180 70 C230 40 260 10 284 20 V166 H0z" fill="var(--green)"/></svg>
  <div class="avatar" role="img" aria-label="Guest portrait" style="background:radial-gradient(circle at 50% 40%,#f0b24a,#b5781e)"></div>
  <h4>Nikos Pavlou</h4>
</article>

<footer>
  <div class="abs rule" style="top:3919px"></div>
  <div class="abs brand foot-brand" style="display:flex"><span class="brand-dot" style="width:40px;height:40px"></span>Corvena Hotel</div>
  <div class="abs contact" style="top:3984px"><svg width="12" height="16" viewBox="0 0 12 16"><path d="M6 0a6 6 0 0 1 6 6c0 4-6 10-6 10S0 10 0 6a6 6 0 0 1 6-6z" fill="#222"/><circle cx="6" cy="6" r="2" fill="#fff"/></svg>12 Filellinon St 40-44, Rhodes 851 00</div>
  <div class="abs contact" style="top:4020px"><svg width="14" height="14" viewBox="0 0 14 14" fill="none" stroke="#222" stroke-width="1.3"><circle cx="7" cy="7" r="6"/><path d="M1 7h12M7 1c3 3 3 9 0 12M7 1c-3 3-3 9 0 12"/></svg>corvenahotel.gr</div>
  <div class="abs contact" style="top:4056px"><svg width="14" height="11" viewBox="0 0 14 11"><rect width="14" height="11" fill="#222"/><path d="M0 0l7 6 7-6" stroke="#fff" fill="none"/></svg>info@corvenahotel.gr</div>
  <div class="abs contact" style="top:4092px"><svg width="14" height="14" viewBox="0 0 14 14"><path d="M3 0l3 3-2 2c1 2 3 4 5 5l2-2 3 3-2 3C6 14 0 8 0 2z" fill="#222"/></svg>(+30) 2241055310-2</div>
  <div class="abs fcol" style="left:750px;top:3952px">
    <h5>QUICK LINKS</h5><a>Home</a><a>Rooms</a><a>Gallery</a><a>Contact</a>
  </div>
  <div class="abs fcol" style="left:934px;top:3952px">
    <h5>HELP LINKS</h5><a>Privacy Policy</a><a>Terms &amp; Conditions</a><a>Support</a><a>About Us</a>
  </div>
  <div class="abs rule" style="top:4159px"></div>
  <p class="abs copy">© copyrights 2022 Corvena Hotel | All Rights Reserved</p>
</footer>

</body>
</html>
```